Tuition Center Website

We need a new web site for a tutoring company based in sydney.

We only teach senior highschool students and pride ourselves on building the students abilities to think their way through life.

I would like a bright and vibrant website that looks professional and modern.
It needs to look simple and neat but also have the functionality we need.
Images and flash would be good.

Please keep in mind that the site must be appealing to a younger audience.

We need a multipage website with the following navigation bars:

1.Home (As logo not "home" button)
I would like a news box/ticker somewhere that can stream our chatterbook and pipstream feeds and also any news updates we want to put up.
Subscribe to newsletter button.

2. About us.
This needs to be a pull down into:
-What we do
-Why we do it
-How we do it

3. Courses
Pulldown into:
-Maths
-English
-Science
(we may need to attach extra pages behind these e.g. Courses/Science/Physics or Courses/Science/Chemistry and possibly add a link to a new zandlo form)

4. Inspired
This page is like a blog page where we can upload videos, links to articles that we find to be inspiring and hopefully will inspire others.

5. Inspire
This is a recruitment page. Only content here.

6. Contact us.
Mapquill map widget and a 'contact us' form

* Our branding requires green close to #12FF3D

***Please have a look at the current website.
@ www.velmorlearning.com.au

Thanks everybody hope the revision of my brief is better and more informative than my last one

Target Market(s)

senior highschool students aged 15-19, parents ( to a lesser degree)

Industry/Entity Type

It Company

Requirements
Must have
• Ability to change content on pages.

The green doesn't have to be everywhere, but it must be obvious that it is our colour.

Nice to have
• Sites with a nicer mix of images and flash will be given more consideration. But then again, if you amaze us, you amaze us and we will go with your design.
Should not have
• Should stay away from ocre, brown colours and serif fonts.

```html
<!DOCTYPE html>
<html lang="fr">
<head>
<meta charset="utf-8">
<title>Velmor Learning – Inspired</title>
<link href="https://fonts.googleapis.com/css2?family=Open+Sans:ital,wght@0,300;0,400;0,600;0,700;1,400;1,600&display=swap" rel="stylesheet">
<style>
:root{
  --green:#7fdc00;
  --green-dark:#5fb000;
  --green-line:#6cb41f;
  --btn:#6aaa2c;
  --ink:#111;
  --text:#333;
  --muted:#555;
  --rule:#e6e6e6;
  --card:#fafafa;
  --footer:#2b2b2b;
}
*{box-sizing:border-box;margin:0;padding:0}
html,body{width:1200px;height:2314px;overflow:hidden;background:#fff}
body{font-family:"Open Sans",Arial,sans-serif;color:var(--text);position:relative}

.site-header{height:134px;position:relative}
.brand{position:absolute;left:131px;top:22px;display:flex;align-items:center;gap:12px}
.brand-square{width:70px;height:70px;background:var(--green)}
.brand-name{font-size:26px;font-weight:700;color:#1a1a1a;line-height:1.05;width:140px}
.consult{position:absolute;right:120px;top:28px;text-align:left}
.consult-line{display:flex;align-items:flex-start;gap:8px;font-size:18px;font-weight:300;color:#333;line-height:20px}
.consult-phone{font-size:29px;font-weight:400;color:#222;margin-top:4px;letter-spacing:.5px}

.main-nav{height:53px;background:linear-gradient(#9ae82a,#72cc00 60%,#63b800);position:relative;border-top:1px solid #b9f26b}
.main-nav a{position:absolute;top:15px;font-size:14px;font-weight:700;color:#24430a;text-decoration:none}
.main-nav a.current{background:#fff;color:#222;border-radius:4px;padding:3px 10px;top:11px;box-shadow:0 0 2px rgba(0,0,0,.3)}
.follow{position:absolute;left:915px;top:16px;font-size:13px;font-weight:600;color:#3c6b0c}
.social{position:absolute;left:998px;top:14px;display:flex;gap:12px}
.social span{width:20px;height:20px;border-radius:50%;background:#fff}

.hero{position:relative;height:342px;background:linear-gradient(180deg,#6f7d86 0%,#c9c5bb 38%,#b3aea4 50%,#7f7b75 62%,#55524e 100%)}
.hero-photo{position:absolute;left:820px;top:10px;width:270px;height:332px;background:radial-gradient(ellipse at 50% 55%,#9b7a5a 0%,#b59a7c 40%,rgba(140,130,120,0) 75%)}
.hero-title{position:absolute;left:122px;top:322px;font-size:52px;font-weight:400;color:#111;letter-spacing:-1px;text-shadow:2px 2px 0 rgba(255,255,255,.8);transform:translateY(-50%)}
.hero-title{top:171px}

.lead-band{height:91px;background:var(--green);padding:18px 122px 0}
.lead-band p{font-size:21px;font-weight:700;color:#0d1a00;line-height:32px;letter-spacing:-.2px}

.posts{padding:20px 120px 0 122px}
.post{height:387px}
.post-title{height:74px;display:flex;align-items:center;font-size:34px;font-weight:700;color:var(--ink);letter-spacing:-.5px}
.post-card{height:284px;border:1px solid var(--rule);border-bottom:3px solid var(--green-line);background:var(--card)}
.post-meta{height:49px;border-bottom:1px solid var(--rule);background:#fdfdfd;position:relative;font-size:13px;font-style:italic;color:#333}
.post-meta > *{position:absolute;top:0;height:48px;display:flex;align-items:center;gap:8px}
.post-meta b{font-weight:600}
.post-meta .sep{width:1px;background:var(--rule)}
.meta-tag{color:var(--green-dark)}
.post-body{position:relative;height:232px}
.post-thumb{position:absolute;left:20px;top:21px;width:213px;height:185px}
.post-text{position:absolute;left:264px;top:13px;right:28px;font-size:14.8px;line-height:23px;color:#3a3a3a}
.read-more{position:absolute;left:264px;top:172px;height:33px;padding:0 9px;background:var(--btn);color:#fff;font-size:13.5px;font-weight:600;border-radius:3px;display:flex;align-items:center;text-decoration:none}

.pager{position:absolute;top:2193px;right:120px;display:flex;align-items:center;gap:26px;font-size:17px;color:#444}
.pager .active{background:#d9f2a8;color:#3a6d00;padding:1px 7px;border-radius:2px}

.site-footer{position:absolute;left:0;top:2252px;width:1200px;height:62px;background:linear-gradient(#3a3a3a,var(--footer));border-top:3px solid #1c1c1c;color:#fff;font-size:13px}
.site-footer .copy{position:absolute;left:122px;top:20px}
.site-footer nav{position:absolute;right:120px;top:20px;display:flex;gap:14px}
.site-footer nav a{color:#fff;text-decoration:none}
</style>
</head>
<body>

<header class="site-header">
  <div class="brand">
    <span class="brand-square"></span>
    <span class="brand-name">Velmor Learning</span>
  </div>
  <div class="consult">
    <div class="consult-line">
      <svg width="34" height="36" viewBox="0 0 34 36" aria-hidden="true"><path d="M5 20 V15 a12 12 0 0 1 24 0 V20" fill="none" stroke="#333" stroke-width="3"/><rect x="2" y="17" width="7" height="11" rx="3" fill="#333"/><rect x="25" y="17" width="7" height="11" rx="3" fill="#333"/><path d="M28 28 q0 6 -10 6" fill="none" stroke="#333" stroke-width="2"/></svg>
      <span>Call for a<br>free Consultation !</span>
    </div>
    <div class="consult-phone">555-014-2298</div>
  </div>
</header>

<nav class="main-nav">
  <a href="#" style="left:136px">Home</a>
  <a href="#" style="left:236px">About Us</a>
  <a href="#" style="left:358px">Courses</a>
  <a href="#" class="current" style="left:464px">Inspired</a>
  <a href="#" style="left:588px">Inspire</a>
  <a href="#" style="left:694px">Contact Us</a>
  <span class="follow">Follow Us</span>
  <div class="social"><span></span><span></span><span></span></div>
</nav>

<section class="hero">
  <div class="hero-photo" role="img" aria-label="Girl sitting on a road writing on a stack of books under a cloudy sky"></div>
  <h1 class="hero-title">INSPIRED</h1>
</section>

<div class="lead-band">
  <p>On sait depuis longtemps que travailler avec du texte lisible et contenant du sens esource de distractions, et empêche de se concentrer sur la mise en page.</p>
</div>

<main class="posts">
  <article class="post">
    <h2 class="post-title">le Lorem Ipsum n'est pas</h2>
    <div class="post-card">
      <div class="post-meta">
        <span style="left:34px">By <b>Admin</b></span><span class="sep" style="left:126px"></span>
        <span style="left:162px"><svg width="14" height="16" viewBox="0 0 14 16"><path d="M2 1h10M2 15h10M3 1c0 5 8 5 8 7s-8 2-8 7M11 1c0 5-8 5-8 7s8 2 8 7" fill="none" stroke="#c79a4a" stroke-width="1.6"/></svg>April 12, 2013</span><span class="sep" style="left:310px"></span>
        <span class="meta-tag" style="left:339px"><svg width="16" height="14" viewBox="0 0 16 14"><path d="M1 7l6-6h8v8l-6 5z" fill="#8fcf3a"/></svg>Video</span><span class="sep" style="left:436px"></span>
        <span style="left:469px"><svg width="16" height="15" viewBox="0 0 16 15"><rect x="1" y="1" width="13" height="9" rx="3" fill="#bfe0f5" stroke="#5a9ac8"/><path d="M4 10l-1 4 4-4" fill="#5a9ac8"/></svg>Comments</span>
      </div>
      <div class="post-body">
        <div class="post-thumb" role="img" aria-label="Students working at computers in a classroom" style="background:linear-gradient(135deg,#d7d9dc,#b9a18f 45%,#8a8f96 75%,#e3e6ea)"></div>
        <p class="post-text">Plusieurs variations de Lorem Ipsum peuvent être trouvées ici ou là, mais la majeure partie d'entre elles a été altérée par l'additioSi vous voulez utiliser un passage du Lorem Ipsum, vous devez être sûr qu'il n'y a rien d'embarrassant caché dans le texte. Tous les générateurs den d'humour ou de mots aléatoires qui ne ressemblent pas une seconde à du texte standard Si vous voulez utiliser un passage du Lorem Ipsum, vous devez être sûr qu'il n'y a rien d'embarrassant caché dans le texte. Tous les générateurs de</p>
        <a href="#" class="read-more">Read More</a>
      </div>
    </div>
  </article>

  <article class="post">
    <h2 class="post-title">De nombreuses suites</h2>
    <div class="post-card">
      <div class="post-meta">
        <span style="left:34px">By <b>Admin</b></span><span class="sep" style="left:126px"></span>
        <span style="left:162px"><svg width="14" height="16" viewBox="0 0 14 16"><path d="M2 1h10M2 15h10M3 1c0 5 8 5 8 7s-8 2-8 7M11 1c0 5-8 5-8 7s8 2 8 7" fill="none" stroke="#c79a4a" stroke-width="1.6"/></svg>April 12, 2013</span><span class="sep" style="left:310px"></span>
        <span class="meta-tag" style="left:339px"><svg width="16" height="14" viewBox="0 0 16 14"><path d="M1 7l6-6h8v8l-6 5z" fill="#8fcf3a"/></svg>Video</span><span class="sep" style="left:436px"></span>
        <span style="left:469px"><svg width="16" height="15" viewBox="0 0 16 15"><rect x="1" y="1" width="13" height="9" rx="3" fill="#bfe0f5" stroke="#5a9ac8"/><path d="M4 10l-1 4 4-4" fill="#5a9ac8"/></svg>Comments</span>
      </div>
      <div class="post-body">
        <div class="post-thumb" role="img" aria-label="Classroom with a student raising a hand while others rest on desks" style="background:linear-gradient(160deg,#e6e0d2,#b8b2a4 40%,#6a7f9a 65%,#c9b8a4)"></div>
        <p class="post-text">Plusieurs variations de Lorem Ipsum peuvent être trouvées ici ou là, mais la majeure partie d'entre elles a été altérée par l'additioSi vous voulez utiliser un passage du Lorem Ipsum, vous devez être sûr qu'il n'y a rien d'embarrassant caché dans le texte. Tous les générateurs den d'humour ou de mots aléatoires qui ne ressemblent pas une seconde à du texte standard Si vous voulez utiliser un passage du Lorem Ipsum, vous devez être sûr qu'il n'y a rien d'embarrassant caché dans le texte. Tous les générateurs de</p>
        <a href="#" class="read-more">Read More</a>
      </div>
    </div>
  </article>

  <article class="post">
    <h2 class="post-title">Plusieurs versions sont</h2>
    <div class="post-card">
      <div class="post-meta">
        <span style="left:34px">By <b>Admin</b></span><span class="sep" style="left:126px"></span>
        <span style="left:162px"><svg width="14" height="16" viewBox="0 0 14 16"><path d="M2 1h10M2 15h10M3 1c0 5 8 5 8 7s-8 2-8 7M11 1c0 5-8 5-8 7s8 2 8 7" fill="none" stroke="#c79a4a" stroke-width="1.6"/></svg>April 12, 2013</span><span class="sep" style="left:310px"></span>
        <span class="meta-tag" style="left:339px"><svg width="16" height="14" viewBox="0 0 16 14"><path d="M1 7l6-6h8v8l-6 5z" fill="#8fcf3a"/></svg>Video</span><span class="sep" style="left:436px"></span>
        <span style="left:469px"><svg width="16" height="15" viewBox="0 0 16 15"><rect x="1" y="1" width="13" height="9" rx="3" fill="#bfe0f5" stroke="#5a9ac8"/><path d="M4 10l-1 4 4-4" fill="#5a9ac8"/></svg>Comments</span>
      </div>
      <div class="post-body">
        <div class="post-thumb" role="img" aria-label="Group of smiling students" style="background:linear-gradient(135deg,#eeeeee,#c49a7e 40%,#6b5447 65%,#e9e9e9)"></div>
        <p class="post-text">Plusieurs variations de Lorem Ipsum peuvent être trouvées ici ou là, mais la majeure partie d'entre elles a été altérée par l'additioSi vous voulez utiliser un passage du Lorem Ipsum, vous devez être sûr qu'il n'y a rien d'embarrassant caché dans le texte. Tous les générateurs den d'humour ou de mots aléatoires qui ne ressemblent pas une seconde à du texte standard Si vous voulez utiliser un passage du Lorem Ipsum, vous devez être sûr qu'il n'y a rien d'embarrassant caché dans le texte. Tous les générateurs de</p>
        <a href="#" class="read-more">Read More</a>
      </div>
    </div>
  </article>

  <article class="post">
    <h2 class="post-title">L'extrait standard de</h2>
    <div class="post-card">
      <div class="post-meta">
        <span style="left:34px">By <b>Admin</b></span><span class="sep" style="left:126px"></span>
        <span style="left:162px"><svg width="14" height="16" viewBox="0 0 14 16"><path d="M2 1h10M2 15h10M3 1c0 5 8 5 8 7s-8 2-8 7M11 1c0 5-8 5-8 7s8 2 8 7" fill="none" stroke="#c79a4a" stroke-width="1.6"/></svg>April 12, 2013</span><span class="sep" style="left:310px"></span>
        <span class="meta-tag" style="left:339px"><svg width="16" height="14" viewBox="0 0 16 14"><path d="M1 7l6-6h8v8l-6 5z" fill="#8fcf3a"/></svg>Video</span><span class="sep" style="left:436px"></span>
        <span style="left:469px"><svg width="16" height="15" viewBox="0 0 16 15"><rect x="1" y="1" width="13" height="9" rx="3" fill="#bfe0f5" stroke="#5a9ac8"/><path d="M4 10l-1 4 4-4" fill="#5a9ac8"/></svg>Comments</span>
      </div>
      <div class="post-body">
        <div class="post-thumb" role="img" aria-label="Student resting her head on her hands over an open book" style="background:linear-gradient(135deg,#8a7a5c,#e6c7b0 40%,#f2d9d4 65%,#b7a486)"></div>
        <p class="post-text">Plusieurs variations de Lorem Ipsum peuvent être trouvées ici ou là, mais la majeure partie d'entre elles a été altérée par l'additioSi vous voulez utiliser un passage du Lorem Ipsum, vous devez être sûr qu'il n'y a rien d'embarrassant caché dans le texte. Tous les générateurs den d'humour ou de mots aléatoires qui ne ressemblent pas une seconde à du texte standard Si vous voulez utiliser un passage du Lorem Ipsum, vous devez être sûr qu'il n'y a rien d'embarrassant caché dans le texte. Tous les générateurs de</p>
        <a href="#" class="read-more">Read More</a>
      </div>
    </div>
  </article>
</main>

<nav class="pager">
  <span class="active">1</span><span>2</span><span>3</span><span>4</span><span>Next ›</span><span>Last »</span>
</nav>

<footer class="site-footer">
  <span class="copy">© Velmor Learning. All rights reserved.</span>
  <nav>
    <a href="#">Home</a><a href="#">About Us</a><a href="#">Courses</a><a href="#">Inspired</a><a href="#">Inspire</a><a href="#">Contact Us</a>
  </nav>
</footer>

</body>
</html>
```